Website redesign for Halt and Fullmane

We would like to update the design of our current website to a more concise, conversion optimized design.
The goal of our website is to get our message across as concisely as possible plus encourage people to contact us for more information or to book a consultation.
We need a redesign of the home page and 1 internal page - just for design/layout purposes/format purposes.

Target Market(s)

Males 20-45 years old who are concerned about hair loss and who want to regrow their own hair.

Industry/Entity Type

Health And Wellness

Number of Pages Required

2 page

Font styles to use
Sans Serif

Colors
00a990
33a6d7
ffffff
9d9d9d

Requirements
Must have
• We want the home page to be very concise and to the point in getting the message across. We want to get across the following 6 key messages:
• 1. Dr Pembrook story – why he created this solution
• 2. Hair loss is caused by a chemical imbalance
• 3. Halt and fullmane conducts genetic and DNA analysis, then rebalances body chemistry, thus reversing the hair loss process and enabling your own hair to regrow naturally
• 4. Money back guaranteed results
• 5. Purely Core ingredients – no harsh preservatives or chemicals are included
• 6. All ingredients are FDA approved and safe – no side effects
• We also need a strong call to action. We want people to call or email us to find out more information or to schedule a consultation.
• Here is our current website which is not performing as we would hope: http://www.haltandfullmane.example/
• Here is our press release for further information: https://www.pressdeskhub.example/news/finally-we-now-have-a-cure-for-male-pattern-baldness-28461902
• I uploaded the logo files, but let me know if anything else is needed and I can add it.

```html
<!DOCTYPE html>
<html lang="en">
<head>
<meta charset="utf-8">
<title>Halt and Fullmane – Home</title>
<link href="https://fonts.googleapis.com/css2?family=Josefin+Sans:wght@400;600&family=Open+Sans:wght@400;600;700&display=swap" rel="stylesheet">
<style>
:root{
  --teal:#00a990;
  --blue:#33a6d7;
  --white:#ffffff;
  --grey:#9d9d9d;
  --ink:#222222;
  --body:#666666;
  --line:#cfcfcf;
  --star:#f5c518;
}
*{box-sizing:border-box;margin:0;padding:0}
html,body{width:1200px;height:2894px;overflow:hidden;background:var(--white)}
body{font-family:"Open Sans",Arial,sans-serif;color:var(--body);position:relative}
.head-font{font-family:"Josefin Sans",Arial,sans-serif}
section,header,footer{position:absolute;left:0;width:1200px}

/* header */
.site-header{top:0;height:88px;border-top:4px solid var(--teal);background:var(--white)}
.brand{position:absolute;left:98px;top:18px;display:flex;align-items:center;gap:10px}
.brand-mark{width:34px;height:34px;border-radius:50%;background:var(--teal)}
.brand-name{font-family:"Josefin Sans",sans-serif;font-size:22px;color:var(--teal);line-height:1.1}
.brand-name small{display:block;font-size:14px}
.social{position:absolute;display:flex;gap:6px}
.social span{width:26px;height:26px;border-radius:50%;display:block}
.header-social{right:270px;top:10px}
.call{position:absolute;right:98px;top:12px;display:flex;align-items:center;gap:10px;font-size:14px;color:var(--ink)}
.call i{width:24px;height:24px;border:1px solid var(--grey);border-radius:50%;display:flex;align-items:center;justify-content:center}
.main-nav{position:absolute;right:98px;top:58px;display:flex;gap:19px;font-family:"Josefin Sans",sans-serif;font-size:16px;color:var(--ink);align-items:center}

/* hero */
.hero{top:88px;height:447px;background:linear-gradient(100deg,#8b8580 0%,#c4b3a4 30%,#6e6a66 55%,#3c3a38 80%,#9a8c82 100%)}
.hero h1{position:absolute;top:128px;width:100%;text-align:center;color:var(--white);font-family:"Josefin Sans",sans-serif;font-weight:400;font-size:42px;line-height:55px;text-shadow:0 1px 3px rgba(0,0,0,.35)}
.btn-teal{background:var(--teal);color:var(--white);font-weight:600;font-size:16px;text-transform:uppercase}
.hero .btn-teal{position:absolute;left:509px;top:262px;width:182px;height:50px;display:flex;align-items:center;justify-content:center}
.dots{position:absolute;top:378px;left:564px;display:flex;gap:6px}
.dots span{width:14px;height:14px;border:2px solid var(--white);border-radius:50%}
.dots span:first-child{background:var(--white)}

/* welcome */
.welcome{top:535px;height:437px}
.welcome h2{position:absolute;left:98px;top:62px;font-family:"Josefin Sans",sans-serif;font-weight:400;font-size:29px;color:var(--ink)}
.welcome p{position:absolute;left:98px;width:460px;font-size:12px;line-height:22px}
.btn-outline{position:absolute;left:98px;top:331px;width:136px;height:39px;border:1px solid var(--grey);color:var(--teal);font-size:12px;font-weight:700;display:flex;align-items:center;justify-content:center}
.video{position:absolute;left:620px;top:67px;width:483px;height:301px;border:1px solid var(--line);padding:6px;background:var(--white)}
.video-still{width:100%;height:100%;background:linear-gradient(135deg,#e8eef2,#d6c7b8 45%,#c9a82c 85%);position:relative}
.play{position:absolute;left:210px;top:115px;width:58px;height:58px;border-radius:50%;background:rgba(0,0,0,.8)}

/* benefits */
.benefits{top:972px;height:483px;background:linear-gradient(90deg,#c9d6e0 0%,#8fb3cc 30%,#4aa6d4 46%,var(--blue) 60%,#2f9fd2 100%)}
.benefits h2{position:absolute;left:555px;top:50px;font-family:"Josefin Sans",sans-serif;font-weight:400;font-size:28px;color:var(--white)}
.benefit-list{position:absolute;left:554px;top:110px;width:580px;list-style:none;color:var(--white);font-size:13px}
.benefit-list li{display:flex;align-items:center;gap:21px;min-height:40px;margin-bottom:14px;line-height:22px}
.benefit-list b{flex:0 0 40px;height:40px;border:2px solid var(--white);border-radius:50%;display:flex;align-items:center;justify-content:center;font-weight:400;font-size:15px}

/* unique */
.unique{top:1455px;height:470px;text-align:center}
.unique h2{position:absolute;top:60px;width:100%;font-family:"Josefin Sans",sans-serif;font-weight:400;font-size:28px;color:var(--ink)}
.unique p{position:absolute;top:112px;left:240px;width:720px;font-size:13px;line-height:25px}
.feature{position:absolute;top:205px;width:240px;text-align:center}
.feature .ring{width:162px;height:162px;margin:0 auto;border:1px solid var(--grey);border-radius:50%;display:flex;align-items:center;justify-content:center}
.feature h3{margin-top:20px;font-family:"Josefin Sans",sans-serif;font-weight:400;font-size:20px;color:var(--ink)}

/* reviews */
.reviews{top:1925px;height:362px;background:var(--teal);color:var(--white)}
.reviews h2{position:absolute;top:60px;width:100%;text-align:center;font-family:"Josefin Sans",sans-serif;font-weight:400;font-size:28px}
.review{position:absolute;top:123px;width:320px}
.avatar{position:absolute;left:0;top:0;width:74px;height:74px;border-radius:50%;border:3px solid var(--white);background:linear-gradient(#d9d9d9,#9a9a9a)}
.review blockquote{position:absolute;left:90px;top:2px;width:240px;font-size:12px;font-style:italic;line-height:22px}
.review blockquote::before{content:"\201C";font-size:24px;font-style:normal;margin-right:6px;vertical-align:-6px}
.review h4{position:absolute;left:90px;top:99px;font-size:11px;font-weight:600;text-transform:uppercase;white-space:nowrap}
.review em{position:absolute;left:90px;top:118px;font-size:10px;white-space:nowrap}
.stars{position:absolute;left:90px;top:143px;display:flex;gap:3px}
.arrow{position:absolute;top:183px;width:36px;height:36px;border:1px solid var(--white);border-radius:50%;display:flex;align-items:center;justify-content:center}

/* contact */
.contact{top:2287px;height:607px}
.contact h2{position:absolute;top:80px;width:100%;text-align:center;font-family:"Josefin Sans",sans-serif;font-weight:400;font-size:28px;color:var(--ink)}
.contact h3{position:absolute;font-size:14px;font-weight:600;color:var(--ink);text-transform:uppercase}
.field-label{position:absolute;font-size:11px;color:var(--body);text-transform:uppercase}
.field{position:absolute;border:1px solid var(--grey);background:var(--white)}
.contact .btn-teal{position:absolute;left:642px;top:440px;width:88px;height:36px;display:flex;align-items:center;justify-content:center;font-size:13px}
.info-row{position:absolute;left:808px;display:flex;align-items:center;gap:22px;font-size:12px;line-height:24px;color:var(--body)}
.info-row i{flex:0 0 36px;height:36px;border:1px solid var(--grey);border-radius:50%;display:flex;align-items:center;justify-content:center}
.hours{position:absolute;left:808px;top:510px;font-size:12px;line-height:28px}
.footer-rule{position:absolute;left:98px;top:518px;width:1004px;border-top:1px solid var(--line)}
.copyright{position:absolute;left:98px;top:557px;font-size:11px}
.footer-social{right:98px;top:548px}
</style>
</head>
<body>

<header class="site-header">
  <div class="brand"><span class="brand-mark"></span><span class="brand-name">Halt and Fullmane<small>by Alan Pembrook M.D.</small></span></div>
  <div class="social header-social">
    <span style="background:#3b5998"></span><span style="background:#1da1f2"></span><span style="background:#dd4b39"></span><span style="background:#0077b5"></span><span style="background:#cc181e"></span><span style="background:#c41200"></span>
  </div>
  <div class="call"><i><svg width="12" height="12" viewBox="0 0 24 24"><path fill="#00a990" d="M6.6 10.8a15 15 0 0 0 6.6 6.6l2.2-2.2c.3-.3.7-.4 1-.2 1.1.4 2.3.6 3.6.6.6 0 1 .4 1 1V20c0 .6-.4 1-1 1A17 17 0 0 1 3 4c0-.6.4-1 1-1h3.5c.6 0 1 .4 1 1 0 1.3.2 2.5.6 3.6.1.3 0 .7-.2 1z"/></svg></i>Call us: (555) 014-2290</div>
  <nav class="main-nav">
    <span>About Us</span><span>How It Works</span><span>Success Stories</span><span>Faqs</span><span>Blog</span><span>Salon Partners</span><span>Book Now</span><span>Contact</span>
    <svg width="14" height="14" viewBox="0 0 24 24"><circle cx="10" cy="10" r="7" fill="none" stroke="#222" stroke-width="3"/><path d="M15 15l6 6" stroke="#222" stroke-width="3"/></svg>
  </nav>
</header>

<section class="hero" role="img" aria-label="Close-up photo of a man combing his thinning hair">
  <h1>The First Non-Surgical Hair Loss Solution<br>With Clinically Proven Results</h1>
  <div class="btn-teal">Get More Info</div>
  <div class="dots"><span></span><span></span><span></span><span></span></div>
</section>

<section class="welcome">
  <h2>Welcome to Halt and Fullmane</h2>
  <p style="top:112px">Dr. Alan Pembrook, the creator of Halt and Fullmane is a renowned hair restoration expert. After seeing first his father and then older brothers thin and go bald, he dedicated his life to finding the cure for hair loss.</p>
  <p style="top:198px">After initially pioneering the single hair method for hair transplant, he determined there must be a non-surgical solution and spent the last 20 years in research and clinical trial and error first creating, then perfecting what is now the Halt and Fullmane solution for hair loss.</p>
  <div class="btn-outline">READ MORE &gt;&gt;</div>
  <div class="video">
    <div class="video-still" role="img" aria-label="Video still of a man in a yellow shirt pointing at his hairline">
      <div class="play"><svg width="58" height="58" viewBox="0 0 58 58"><path d="M23 18l17 11-17 11z" fill="#fff"/></svg></div>
    </div>
  </div>
</section>

<section class="benefits">
  <div role="img" aria-label="Illustration of hair shafts with a golden strand wrapped around one" style="position:absolute;left:0;top:0;width:520px;height:483px"></div>
  <h2>Six Key Benefits</h2>
  <ol class="benefit-list">
    <li><b>1</b>Dr Pembrook story – why he created this solution</li>
    <li><b>2</b>Hair loss is caused by a chemical imbalance</li>
    <li><b>3</b>Halt and fullmane conducts genetic and DNA analysis, then rebalances body chemistry, thus reversing the hair loss process and enabling your own hair to regrow naturally</li>
    <li><b>4</b>Money back guaranteed results</li>
    <li><b>5</b>Purely Core ingredients – no harsh preservatives or chemicals are included</li>
    <li><b>6</b>All ingredients are FDA approved and safe – no side effects</li>
  </ol>
</section>

<section class="unique">
  <h2>Why Is Halt and Fullmane Unique?</h2>
  <p>Halt and Fullmane uses a scientific approach to hair loss by treating your unique cause. Every case is different and may include multiple causes. Unless we are treating yours, the treatment won't work for you.</p>
  <div class="feature" style="left:63px">
    <div class="ring"><svg width="54" height="54" viewBox="0 0 54 54"><path d="M20 6h14M23 6v16L9 46c-1 2 0 4 3 4h30c3 0 4-2 3-4L31 22V6z" fill="#00a990"/></svg></div>
    <h3>Scientific Approach</h3>
  </div>
  <div class="feature" style="left:340px">
    <div class="ring"><svg width="70" height="60" viewBox="0 0 70 60"><g fill="#00a990"><circle cx="25" cy="34" r="15"/><circle cx="52" cy="16" r="10"/><circle cx="54" cy="44" r="8"/></g><g fill="#fff"><circle cx="25" cy="34" r="6"/><circle cx="52" cy="16" r="4"/><circle cx="54" cy="44" r="3"/></g><g stroke="#00a990" stroke-width="6"><path d="M25 15v38M6 34h38M12 21l26 26M38 21L12 47"/></g><circle cx="25" cy="34" r="6" fill="#fff"/></svg></div>
    <h3>Advanced Technology</h3>
  </div>
  <div class="feature" style="left:618px">
    <div class="ring"><svg width="66" height="54" viewBox="0 0 66 54"><g fill="#00a990"><circle cx="33" cy="14" r="9"/><circle cx="13" cy="19" r="7"/><circle cx="53" cy="19" r="7"/><path d="M18 52c0-12 6-20 15-20s15 8 15 20z"/><path d="M0 48c0-10 5-16 13-16 4 0 6 1 8 3-3 4-5 9-5 13z"/><path d="M66 48c0-10-5-16-13-16-4 0-6 1-8 3 3 4 5 9 5 13z"/></g></svg></div>
    <h3>Personalized Solution</h3>
  </div>
  <div class="feature" style="left:895px">
    <div class="ring"><svg width="64" height="44" viewBox="0 0 64 44"><rect width="64" height="44" fill="#00a990"/><rect x="6" y="6" width="52" height="32" fill="none" stroke="#fff" stroke-width="2"/><circle cx="32" cy="22" r="11" fill="#fff"/><path d="M30 16h3v12" stroke="#00a990" stroke-width="3" fill="none"/></svg></div>
    <h3>Money Back Guarantee</h3>
  </div>
</section>

<section class="reviews">
  <h2>Customer Reviews</h2>
  <div class="arrow" style="left:30px"><svg width="10" height="14" viewBox="0 0 10 14"><path d="M8 1L2 7l6 6" stroke="#fff" stroke-width="2" fill="none"/></svg></div>
  <div class="arrow" style="left:1134px"><svg width="10" height="14" viewBox="0 0 10 14"><path d="M2 1l6 6-6 6" stroke="#fff" stroke-width="2" fill="none"/></svg></div>

  <div class="review" style="left:98px">
    <div class="avatar" role="img" aria-label="Customer portrait photo"></div>
    <blockquote>At vero eos et accusamus et iustodio dignissimos ducimus qui blanditiipraesnt ium voluptatum deleniti atq.</blockquote>
    <h4>Marissa Delane</h4><em>Financial Services Professional</em>
    <div class="stars"><svg width="100" height="18" viewBox="0 0 100 18"><g fill="#f5c518"><path id="s" d="M9 1l2.4 5.3 5.6.6-4.2 3.8 1.2 5.6L9 13.5 4 16.3l1.2-5.6L1 6.9l5.6-.6z"/><use href="#s" x="20"/><use href="#s" x="40"/><use href="#s" x="60"/></g><use href="#s" x="80" fill="none" stroke="#f5c518"/></svg></div>
  </div>
  <div class="review" style="left:445px">
    <div class="avatar" role="img" aria-label="Customer portrait photo"></div>
    <blockquote>At vero eos et accusamus et iustodio dignissimos ducimus qui blanditiipraesnt ium voluptatum deleniti atqu.</blockquote>
    <h4>Teodor R. Valcourt</h4><em>National Urban Fellow at the Houston</em>
    <div class="stars"><svg width="100" height="18" viewBox="0 0 100 18"><g fill="#f5c518"><use href="#s"/><use href="#s" x="20"/><use href="#s" x="40"/><use href="#s" x="60"/></g><use href="#s" x="80" fill="#f5c518" opacity=".55"/></svg></div>
  </div>
  <div class="review" style="left:793px">
    <div class="avatar" role="img" aria-label="Customer portrait photo"></div>
    <blockquote>At vero eos et accusamus et iustodio dignissimos ducimus qui blanditiipraesnt ium voluptatum deleniti atq.</blockquote>
    <h4>Ruth Kessing</h4><em>Creative Strategist | Entrepreneur &amp; Upcoming</em>
    <div class="stars"><svg width="100" height="18" viewBox="0 0 100 18"><g fill="#f5c518"><use href="#s"/><use href="#s" x="20"/><use href="#s" x="40"/><use href="#s" x="60"/></g><use href="#s" x="80" fill="none" stroke="#f5c518"/></svg></div>
  </div>
</section>

<section class="contact">
  <h2>Contact Us</h2>
  <h3 style="left:98px;top:150px">Contact Form</h3>
  <span class="field-label" style="left:98px;top:192px">Name :</span>
  <span class="field-label" style="left:418px;top:192px">Phone No :</span>
  <div class="field" style="left:100px;top:218px;width:311px;height:34px"></div>
  <div class="field" style="left:419px;top:218px;width:311px;height:34px"></div>
  <span class="field-label" style="left:98px;top:264px">Email :</span>
  <div class="field" style="left:100px;top:287px;width:630px;height:34px"></div>
  <span class="field-label" style="left:98px;top:333px">Message :</span>
  <div class="field" style="left:100px;top:356px;width:630px;height:78px"></div>
  <div class="btn-teal">Submit</div>

  <h3 style="left:808px;top:150px">Contact Information</h3>
  <div class="info-row" style="top:190px"><i><svg width="12" height="16" viewBox="0 0 12 16"><path d="M6 0a6 6 0 0 1 6 6c0 4-6 10-6 10S0 10 0 6a6 6 0 0 1 6-6z" fill="none" stroke="#00a990" stroke-width="1.6"/><circle cx="6" cy="6" r="2" fill="#00a990"/></svg></i><span>1280 Larkspur Ave, Suite 300<br>Westbrook CA 90000</span></div>
  <div class="info-row" style="top:253px"><i><svg width="16" height="12" viewBox="0 0 16 12"><rect width="16" height="12" rx="2" fill="#00a990"/><path d="M1 1l7 6 7-6" stroke="#fff" fill="none"/></svg></i><span>info@haltandfullmane.example</span></div>
  <div class="info-row" style="top:306px"><i><svg width="14" height="14" viewBox="0 0 24 24"><path fill="#00a990" d="M6.6 10.8a15 15 0 0 0 6.6 6.6l2.2-2.2c.3-.3.7-.4 1-.2 1.1.4 2.3.6 3.6.6.6 0 1 .4 1 1V20c0 .6-.4 1-1 1A17 17 0 0 1 3 4c0-.6.4-1 1-1h3.5c.6 0 1 .4 1 1 0 1.3.2 2.5.6 3.6.1.3 0 .7-.2 1z"/></svg></i><span>(555) 014-2290</span></div>
  <h3 style="left:808px;top:376px">Opening Hours</h3>
  <div class="hours" style="top:406px">Monday - Friday: 9.00am to 5.00pm<br>Saturday: 8.00am to 2.00pm</div>

  <div class="footer-rule"></div>
  <div class="copyright">Copyrights © 2017, Halt and Fullmane . All Rights Reserved.</div>
  <div class="social footer-social">
    <span style="background:#3b5998"></span><span style="background:#1da1f2"></span><span style="background:#dd4b39"></span><span style="background:#0077b5"></span><span style="background:#cc181e"></span><span style="background:#c41200"></span>
  </div>
</section>

</body>
</html>
```